refurbishment of diamond cut alloy wheels

we need to design a flyer that will catch the eye of the customer to refurbish diamond cut alloy wheels. we refurbish the wheels by using the latest CNC machine to precision cut and resurface the wheel. we would like before and after pictures of maybe Valtoren, KRT, Pelo wheels to give it a prestige look. The final design should communicate an expensive look and providing a good image for the business. The colours that I would like to use is black and red which should make the flyer stand out. The logo must sit on a black background without the wordings of specialists in GX, Pelo etc and also without servicing, diagnostics etc as well. This flyer is just to communicate refurbishment of alloy wheels to high standard.

Target Market(s)

any members of the public and car dealerships

Industry/Entity Type

Automotive

Colors

Requirements
Must have
• Wow factor with great images of wheels
Nice to have
• Maybe on the front of the flyer it has a picture of a wheel and then on the back of the flyer it has before and after pictures to show how just how incredible it is to refurbish wheels
Should not have
• other makes of wheels apart from KRT, Pelo, and any other high end makes of vehicles wheels

```html
<!DOCTYPE html>
<html lang="en">
<head>
<meta charset="utf-8">
<title>Ridgeway Motors – Alloy Wheel Refurbishment Flyer</title>
<link href="https://fonts.googleapis.com/css2?family=Oswald:wght@500;600;700&family=Open+Sans:wght@400;600&display=swap" rel="stylesheet">
<style>
  :root{
    --page:#e9e7e4;
    --black:#0b0b0c;
    --panel:#161618;
    --red:#d3141c;
    --silver:#c9cbcf;
    --white:#ffffff;
    --muted:#d8d8d8;
  }
  *{box-sizing:border-box;margin:0;padding:0}
  html,body{width:1200px;height:834px;overflow:hidden;background:var(--page)}
  body{position:relative;font-family:"Open Sans",Arial,sans-serif}

  .flyer{position:absolute;top:62px;width:500px;height:705px;background:var(--black);overflow:hidden;box-shadow:0 6px 18px rgba(0,0,0,.35)}
  .flyer--front{left:81px}
  .flyer--back{left:631px}

  .brand{position:absolute;top:42px;left:0;width:100%;display:flex;justify-content:center;align-items:center;gap:10px;z-index:3}
  .brand__mark{width:24px;height:24px;background:var(--red)}
  .brand__name{font-family:"Oswald",sans-serif;font-weight:700;font-size:32px;color:var(--white);letter-spacing:1px;text-transform:uppercase}

  .photo{position:absolute}
  .photo--car{top:110px;left:0;width:500px;height:240px;background:radial-gradient(ellipse at 45% 55%,#b5141c 0%,#5a0b0f 35%,#1a1a1c 70%,#0b0b0c 100%)}
  .photo--wheels{top:120px;left:12px;width:476px;height:180px;background:radial-gradient(circle at 18% 50%,#8a8c90 0%,#2b2c2f 22%,transparent 24%),radial-gradient(circle at 50% 50%,#c4c6ca 0%,#5b5d61 22%,transparent 24%),radial-gradient(circle at 82% 50%,#a3a5a9 0%,#3a3b3e 22%,transparent 24%),linear-gradient(#0b0b0c,#1c1c1f)}

  .chevron{position:absolute;left:0;width:500px;height:120px}
  .flyer--front .chevron{top:282px}
  .flyer--back .chevron{top:290px}

  .headline{position:absolute;top:452px;left:0;width:100%;text-align:center;font-family:"Oswald",sans-serif;font-weight:600;font-size:21px;color:var(--white);text-transform:uppercase;letter-spacing:.3px}

  .intro{position:absolute;top:490px;left:18px;width:300px;color:var(--muted);font-size:10.2px;line-height:1.42}
  .intro p+p{margin-top:10px}

  .compare{position:absolute;left:336px;width:146px;height:60px;border-radius:8px;border:1px solid #555}
  .compare--before{top:490px;background:radial-gradient(circle at 55% 55%,#b9a58a 0%,#6d6150 45%,#2a2a2a 100%)}
  .compare--after{top:557px;background:radial-gradient(circle at 55% 55%,#f1f2f4 0%,#a9acb1 45%,#3a3a3c 100%)}
  .compare__tag{position:absolute;top:6px;left:-4px;background:var(--red);color:var(--white);font-family:"Oswald",sans-serif;font-size:9px;font-weight:600;padding:1px 8px}

  .features{position:absolute;top:404px;left:13px;width:474px;display:grid;grid-template-columns:1fr 1fr;gap:10px}
  .feature{position:relative;height:105px;border-radius:8px;overflow:hidden;background:linear-gradient(100deg,#2a2a2d 0%,#19191b 60%,#0e0e10 100%);border:1px solid #3a3a3d}
  .feature__text{position:absolute;top:10px;left:9px;width:132px}
  .feature__title{font-family:"Oswald",sans-serif;font-weight:500;font-size:9.6px;line-height:1.5;color:var(--white);text-transform:uppercase}
  .feature__body{margin-top:6px;font-size:6.6px;line-height:1.4;color:var(--muted)}
  .feature__photo{position:absolute;top:0;right:0;width:92px;height:100%;background:radial-gradient(circle at 55% 50%,#c9cbcf 0%,#6c6f74 40%,#1a1a1c 75%)}
  .feature:nth-child(2) .feature__photo{background:radial-gradient(circle at 55% 50%,#4a4c50 0%,#2a2b2e 40%,#141416 75%)}
  .feature:nth-child(3) .feature__photo{background:radial-gradient(circle at 55% 50%,#c9b48e 0%,#6b6657 40%,#1a1a1c 75%)}

  .contact{position:absolute;top:636px;left:0;width:100%;text-align:center}
  .contact__call{font-family:"Oswald",sans-serif;font-weight:500;font-size:10.5px;color:var(--red);text-transform:uppercase}
  .contact__links{margin-top:2px;font-size:10px;color:var(--white)}

  .footer{position:absolute;bottom:0;left:0;width:100%;height:30px;display:flex;align-items:center}
  .footer__address{height:30px;width:320px;background:var(--red);clip-path:polygon(0 0,100% 0,94% 100%,0 100%);display:flex;align-items:center;gap:6px;padding-left:10px;color:var(--white);font-size:9px;font-weight:600;white-space:nowrap}
  .footer__phone{margin-left:auto;margin-right:16px;display:flex;align-items:center;gap:6px;font-family:"Oswald",sans-serif;font-weight:500;font-size:17px;color:var(--white);letter-spacing:.5px}
  .icon{width:14px;height:14px;flex:none}
</style>
</head>
<body>

<section class="flyer flyer--front">
  <div class="photo photo--car" role="img" aria-label="Red sports coupe on a dark studio floor"></div>
  <div class="brand"><span class="brand__mark"></span><span class="brand__name">Ridgeway Motors</span></div>
  <svg class="chevron" viewBox="0 0 535 120" preserveAspectRatio="none" aria-hidden="true">
    <polygon points="0,20 267,100 535,20 535,120 0,120" fill="#161618"/>
    <polygon points="0,0 267,80 535,0 535,18 267,100 0,18" fill="#b9bbbf"/>
    <polygon points="0,0 267,80 535,0 535,6 267,86 0,6" fill="#e6e7ea"/>
    <polygon points="60,38 267,100 360,72 360,80 267,110 60,48" fill="#d3141c"/>
  </svg>
  <h1 class="headline">Refurbishment of Diamond Cut Alloy Wheels</h1>
  <div class="intro">
    <p>If you are looking to refresh the look of your car but don't want the expense of new alloys, with a wide range of limited edition colours to choose from why not consider customising and refurbishing your existing alloys?</p>
    <p>At Ridgeway Motors, we stock an extensive range of the latest designs from all the leading suppliers and manufacturers so you are sure to find a stylish new design. We can also fix dents, scrapes and severe body damage on your car.</p>
  </div>
  <div class="compare compare--before" role="img" aria-label="Worn alloy wheel before refurbishment"><span class="compare__tag">BEFORE</span></div>
  <div class="compare compare--after" role="img" aria-label="Polished alloy wheel after refurbishment"><span class="compare__tag">AFTER</span></div>
  <div class="contact">
    <p class="contact__call">If you need premier alloy refurbishment services in Marston, please contact us:</p>
    <p class="contact__links">www.ridgewaymotors.co.uk | Dan@ridgewaymotors.co.uk</p>
  </div>
  <div class="footer">
    <div class="footer__address">
      <svg class="icon" viewBox="0 0 24 24"><path fill="#fff" d="M12 2a7 7 0 0 0-7 7c0 5 7 13 7 13s7-8 7-13a7 7 0 0 0-7-7zm0 9.5A2.5 2.5 0 1 1 12 6.5a2.5 2.5 0 0 1 0 5z"/></svg>
      14 Alder Lane, Marston, Westshire, MR4 2JD
    </div>
    <div class="footer__phone">
      <svg class="icon" viewBox="0 0 24 24"><circle cx="12" cy="12" r="11" fill="none" stroke="#fff" stroke-width="2"/><path fill="#fff" d="M9 6.5l1.6 3-1.2 1.2a8 8 0 0 0 3.9 3.9l1.2-1.2 3 1.6-.6 2.3c-4.8.3-9.8-4.7-9.5-9.5z"/></svg>
      01632 960418
    </div>
  </div>
</section>

<section class="flyer flyer--back">
  <div class="brand"><span class="brand__mark"></span><span class="brand__name">Ridgeway Motors</span></div>
  <div class="photo photo--wheels" role="img" aria-label="Three premium multi-spoke alloy wheels in black and silver"></div>
  <svg class="chevron" viewBox="0 0 535 120" preserveAspectRatio="none" aria-hidden="true">
    <polygon points="0,0 267,80 535,0 535,18 267,100 0,18" fill="#b9bbbf"/>
    <polygon points="0,0 267,80 535,0 535,6 267,86 0,6" fill="#e6e7ea"/>
    <polygon points="175,72 267,100 460,42 460,52 267,110 175,82" fill="#d3141c"/>
  </svg>
  <div class="features">
    <article class="feature">
      <div class="feature__text">
        <h2 class="feature__title">Refurbish old or new<br>alloy wheels to perfection</h2>
        <p class="feature__body">We can also supply replacement split rim outer rims, stainless steel wheel trims, titanium and alloy wheel bolts.</p>
      </div>
      <div class="feature__photo" role="img" aria-label="Silver alloy wheel"></div>
    </article>
    <article class="feature">
      <div class="feature__text">
        <h2 class="feature__title">Pure styling with a<br>touch of class...</h2>
        <p class="feature__body">Using an advanced refurbishment technique, we offer unique color-coding.</p>
      </div>
      <div class="feature__photo" role="img" aria-label="Dark grey custom alloy wheel"></div>
    </article>
    <article class="feature">
      <div class="feature__text">
        <h2 class="feature__title">We can fix, respray &amp; repair<br>damaged alloy wheels</h2>
        <p class="feature__body">With our advanced technology, alloy wheel bolts, and studs.</p>
      </div>
      <div class="feature__photo" role="img" aria-label="Damaged alloy wheel awaiting repair"></div>
    </article>
    <article class="feature">
      <div class="feature__text">
        <h2 class="feature__title">Fast affordable friendly<br>service</h2>
        <p class="feature__body">We cater to all locations in and around Marston, Elmsbury, Fenwick, Harrowby, Ashcombe, Wrenfield and Kestleigh.</p>
      </div>
      <div class="feature__photo" role="img" aria-label="Polished multi-spoke alloy wheel"></div>
    </article>
  </div>
  <div class="contact">
    <p class="contact__call">If you need premier alloy refurbishment services in Marston, please contact us:</p>
    <p class="contact__links">www.ridgewaymotors.co.uk | Dan@ridgewaymotors.co.uk</p>
  </div>
  <div class="footer">
    <div class="footer__address">
      <svg class="icon" viewBox="0 0 24 24"><path fill="#fff" d="M12 2a7 7 0 0 0-7 7c0 5 7 13 7 13s7-8 7-13a7 7 0 0 0-7-7zm0 9.5A2.5 2.5 0 1 1 12 6.5a2.5 2.5 0 0 1 0 5z"/></svg>
      14 Alder Lane, Marston, Westshire, MR4 2JD
    </div>
    <div class="footer__phone">
      <svg class="icon" viewBox="0 0 24 24"><circle cx="12" cy="12" r="11" fill="none" stroke="#fff" stroke-width="2"/><path fill="#fff" d="M9 6.5l1.6 3-1.2 1.2a8 8 0 0 0 3.9 3.9l1.2-1.2 3 1.6-.6 2.3c-4.8.3-9.8-4.7-9.5-9.5z"/></svg>
      01632 960418
    </div>
  </div>
</section>

</body>
</html>
```